Lorvex Tilo medical cannibis cultivation company

tag - Tilo rise
Lorvex Tilo medical cannabis cultivation - logo is selected- can we please see bold examples with our selection. We are mainly dealing with medical companies and professionals. We would like to be stand out in the crowd with our designs. Welcome any and all attempts. Thanks

Target Market(s)

Medical and Professional

Industry/Entity Type

Medical And Science

Font styles to use
Sans Serif

Colors

Designer to choose colors to be used in the design.

Requirements
Must have
• Bright colour and be bold- Love the teal and magenta that is currently on the dark background design.
Nice to have
• shading and the 3D affect- The shadowed appearance.
Should not have
• Anything related to illegal activity or un professional manners

```html
<!DOCTYPE html>
<html lang="en">
<head>
<meta charset="utf-8">
<title>Lorvex Tilo – Business Card</title>
<link rel="stylesheet" href="https://fonts.googleapis.com/css2?family=Roboto:wght@400;500;700&display=swap">
<style>
  :root {
    --page: #eeeae4;
    --card-white: #ffffff;
    --card-black: #000000;
    --cyan: #1ab0e6;
    --magenta: #a54ca8;
    --text-grey: #555a5e;
    --ring-grey: #9aa0a6;
    --divider: #c9cdd0;
    --web-grey: #c9ccd0;
  }
  * { box-sizing: border-box; margin: 0; padding: 0; }
  html, body {
    width: 1125px; height: 1200px; overflow: hidden;
    background: var(--page);
    font-family: "Roboto", Arial, sans-serif;
  }
  .canvas { position: relative; width: 1125px; height: 1200px; }

  .card {
    position: absolute; left: 151px; width: 823px; height: 470px;
    border-radius: 22px; overflow: hidden;
    box-shadow: 0 6px 18px rgba(0,0,0,0.18);
  }
  .card--front { top: 98px; background: var(--card-white); }
  .card--back { top: 632px; background: var(--card-black); }

  /* front: brand block */
  .brand {
    position: absolute; left: 40px; width: 410px; top: 110px;
    display: flex; flex-direction: column; align-items: center;
  }
  .brand__dot {
    width: 150px; height: 150px; border-radius: 50%;
    border: 7px solid var(--ring-grey);
  }
  .brand__name {
    margin-top: 26px; font-size: 44px; font-weight: 500;
    color: var(--cyan); letter-spacing: 1px; white-space: nowrap;
  }
  .brand__tag {
    margin-top: 4px; display: flex; align-items: center; gap: 10px;
    font-size: 19px; color: var(--ring-grey); letter-spacing: 2px; text-transform: uppercase;
  }
  .brand__tag::before, .brand__tag::after {
    content: ""; width: 60px; height: 2px; background: var(--ring-grey);
  }

  .divider {
    position: absolute; left: 450px; top: 92px; width: 2px; height: 290px;
    background: var(--divider);
  }

  .contact { position: absolute; left: 494px; top: 100px; color: var(--text-grey); }
  .contact__name { font-size: 31px; font-weight: 700; color: var(--cyan); letter-spacing: 0.5px; }
  .contact__role { font-size: 20px; font-weight: 500; color: var(--magenta); margin-top: 2px; }
  .contact__address { font-size: 19.5px; line-height: 25px; margin-top: 16px; }
  .contact__list { list-style: none; margin-top: 16px; }
  .contact__item { display: flex; align-items: center; font-size: 19.5px; height: 26px; }
  .contact__icon { width: 18px; height: 18px; margin-right: 13px; fill: var(--cyan); flex: none; }

  .edge-line { position: absolute; left: 0; right: 0; bottom: 18px; height: 3px; background: var(--magenta); }
  .edge-band { position: absolute; left: 0; right: 0; bottom: 0; height: 16px; background: var(--cyan); }

  /* back */
  .back-mark {
    position: absolute; left: 0; right: 0; top: 105px;
    display: flex; flex-direction: column; align-items: center;
  }
  .back-mark__dot {
    width: 150px; height: 150px; border-radius: 50%;
    border: 7px solid var(--ring-grey);
  }
  .back-mark__name {
    margin-top: 26px; font-size: 44px; font-weight: 500;
    color: var(--cyan); letter-spacing: 1px;
  }
  .back-web {
    position: absolute; left: 0; right: 0; top: 400px; text-align: center;
    font-size: 18px; letter-spacing: 5px; color: var(--web-grey);
  }
</style>
</head>
<body>
<div class="canvas">

  <section class="card card--front">
    <div class="brand">
      <div class="brand__dot"></div>
      <div class="brand__name">LORVEX TILO</div>
      <div class="brand__tag">Tilo rise</div>
    </div>

    <div class="divider"></div>

    <div class="contact">
      <div class="contact__name">DAREN HOLT</div>
      <div class="contact__role">CEO/FOUNDER</div>
      <div class="contact__address">4120 Kestrel Avenue<br>Fairbanks, Alaska 34590</div>
      <ul class="contact__list">
        <li class="contact__item">
          <svg class="contact__icon" viewBox="0 0 24 24"><path d="M6.6 10.8c1.4 2.8 3.8 5.1 6.6 6.6l2.2-2.2c.3-.3.7-.4 1-.2 1.1.4 2.3.6 3.6.6.6 0 1 .4 1 1V20c0 .6-.4 1-1 1C10.6 21 3 13.4 3 4c0-.6.4-1 1-1h3.5c.6 0 1 .4 1 1 0 1.3.2 2.5.6 3.6.1.3 0 .7-.2 1z"/></svg>
          614 220 7381
        </li>
        <li class="contact__item">
          <svg class="contact__icon" viewBox="0 0 24 24"><path d="M7 1h10a2 2 0 0 1 2 2v18a2 2 0 0 1-2 2H7a2 2 0 0 1-2-2V3a2 2 0 0 1 2-2zm0 3v14h10V4zm5 15.5a1.2 1.2 0 1 0 0 2.4 1.2 1.2 0 0 0 0-2.4z"/></svg>
          752 309 4416
        </li>
        <li class="contact__item">
          <svg class="contact__icon" viewBox="0 0 24 24"><path d="M6 2h12v5H6zM3 8h18a2 2 0 0 1 2 2v7h-4v5H5v-5H1v-7a2 2 0 0 1 2-2zm4 8v4h10v-4z"/></svg>
          538 174 2069
        </li>
        <li class="contact__item">
          <svg class="contact__icon" viewBox="0 0 24 24"><path d="M2 5h20v14H2zm2 2v.5l8 5 8-5V7l-8 5z"/></svg>
          daren@lorvextilo.com
        </li>
        <li class="contact__item">
          <svg class="contact__icon" viewBox="0 0 24 24"><circle cx="12" cy="12" r="10"/><path d="M12 2c-3 3-3 17 0 20M2 12h20M4 7h16M4 17h16" stroke="#fff" stroke-width="1.3" fill="none"/></svg>
          www.lorvextilo.com
        </li>
      </ul>
    </div>

    <div class="edge-line"></div>
    <div class="edge-band"></div>
  </section>

  <section class="card card--back">
    <div class="back-mark">
      <div class="back-mark__dot"></div>
      <div class="back-mark__name">LORVEX TILO</div>
    </div>
    <div class="back-web">www.lorvextilorise.com</div>
  </section>

</div>
</body>
</html>
```